KAJU Freightways #ALLKAJU Business Cards & Letterhead

I am looking to business cards designed for our organization. We are currently undergoing a small re-branding that is taking place. Our organization is called KAJU Freightways and we are headquartered in Phoenix, AZ. We primarily provide transportation and logistics services to the Marlow Parcel Bureau who is our largest customer. I would like to see a design that incorporates name, title, contact info, website, and address (this will be different depending on the employee). I would also like to see some color on the business card using our logo colors or a variation. I would like our logo on the back of the business card with the website displayed. The final design should communicate that we are a next generation transportation operate that focuses on being driver-first, customer-centric, innovative, and sustainable.We would also like our #ALLKAJU catch phrase incorporated as well.

Target Market(s)

Transportation & Logistics

Industry/Entity Type

Trucking Company

Contact Information for Business Card

-First and Last Name
-Position Title
-Contact Phone
-Contact Email
-Physical Address

Font styles to use
Serif

Colors

Designer to choose colors to be used in the design.

Requirements
Must have
• -KAJU logo prominently displayed
• -#ALLKAJU catch phrase used
• -Some amount of color, design gradient, etc.
• -Logo on the back with website listed (https://www.kajufreightco.example)

```html
<!DOCTYPE html>
<html lang="en">
<head>
<meta charset="utf-8">
<title>KAJU Freightways Business Card</title>
<link rel="stylesheet" href="https://fonts.googleapis.com/css2?family=Roboto+Slab:wght@400;600;800&display=swap">
<style>
  :root {
    --backdrop: #808080;
    --card-white: #ffffff;
    --deep-teal: #023a47;
    --leaf-green: #7cc242;
    --ink: #1f2a2e;
  }
  html, body {
    margin: 0;
    padding: 0;
    overflow: hidden;
    background: var(--backdrop);
  }
  .canvas {
    position: relative;
    width: 1200px;
    height: 1020px;
    overflow: hidden;
    background: var(--backdrop);
    font-family: "Roboto Slab", Georgia, serif;
  }
  .card-shapes {
    position: absolute;
    inset: 0;
  }
  .holder-name {
    position: absolute;
    left: 294px;
    top: 128px;
    margin: 0;
    font-size: 27px;
    font-weight: 600;
    color: var(--deep-teal);
    line-height: 1;
  }
  .holder-title {
    position: absolute;
    left: 295px;
    top: 161px;
    margin: 0;
    font-size: 17px;
    font-weight: 400;
    color: var(--ink);
    line-height: 1;
  }
  .address {
    position: absolute;
    left: 295px;
    top: 303px;
    margin: 0;
    font-size: 16.5px;
    line-height: 23px;
    color: var(--ink);
    font-style: normal;
  }
  .contact-list {
    position: absolute;
    left: 317px;
    top: 367px;
    margin: 0;
    padding: 0;
    list-style: none;
    font-size: 16px;
    line-height: 25.5px;
    color: var(--ink);
  }
  .wordmark {
    position: absolute;
    left: 554px;
    width: 374px;
    text-align: center;
    margin: 0;
    font-weight: 800;
    font-size: 104px;
    line-height: 1;
    letter-spacing: 1px;
  }
  .wordmark--front { top: 222px; color: var(--deep-teal); }
  .wordmark--back { top: 647px; color: var(--card-white); }
  .catchphrase {
    position: absolute;
    left: 296px;
    top: 800px;
    margin: 0;
    font-size: 24px;
    font-weight: 800;
    line-height: 1;
    color: var(--leaf-green);
  }
  .back-website {
    position: absolute;
    left: 296px;
    top: 838px;
    margin: 0;
    font-size: 15px;
    font-weight: 400;
    line-height: 1;
    color: var(--card-white);
  }
</style>
</head>
<body>
<div class="canvas">
  <svg class="card-shapes" width="1200" height="1020" viewBox="0 0 1200 1020" aria-hidden="true">
    <rect x="272" y="88" width="470" height="377" fill="var(--card-white)"/>
    <circle cx="741" cy="276" r="188" fill="var(--leaf-green)"/>
    <circle cx="741" cy="276" r="176" fill="var(--card-white)"/>
    <rect x="271" y="514" width="471" height="375" fill="var(--deep-teal)"/>
    <circle cx="741" cy="701" r="188" fill="var(--card-white)"/>
    <circle cx="741" cy="701" r="176" fill="var(--deep-teal)"/>
    <g fill="var(--deep-teal)">
      <path d="M296 375.5c0 5 4 9 9 9l1.8-2.3-2.6-2-1.3 1.2a7 7 0 0 1-3.2-3.2l1.2-1.3-2-2.6z"/>
      <path d="M303 373.5a4 4 0 0 1 4 4h-1.2a2.8 2.8 0 0 0-2.8-2.8z"/>
      <rect x="296" y="401" width="12" height="9"/>
      <circle cx="301.5" cy="430.5" r="6.2"/>
    </g>
    <path d="M296.5 401.8l5.5 4.3 5.5-4.3" fill="none" stroke="var(--card-white)" stroke-width="1.1"/>
    <path d="M296 430.5h11M301.5 424.5c-3 3.5-3 8.5 0 12M301.5 424.5c3 3.5 3 8.5 0 12" fill="none" stroke="var(--card-white)" stroke-width="0.9"/>
  </svg>

  <h1 class="holder-name">Dana Whitcombe</h1>
  <p class="holder-title">Owner</p>
  <address class="address">418, Larkspur Road<br>Phoenix AZ 85004, US</address>
  <ul class="contact-list">
    <li>(602) 555-0147</li>
    <li>dana@kajufreightco.example</li>
    <li>www.kajufreightco.example</li>
  </ul>

  <p class="wordmark wordmark--front">KAJU</p>
  <p class="wordmark wordmark--back">KAJU</p>
  <p class="catchphrase">#ALLKAJU</p>
  <p class="back-website">https://www.kajufreightco.example</p>
</div>
</body>
</html>
```